Dietitian needs awesome business card

I need a contemporary design that's eye catching but professional.
My card is to given to doctors, specialists and patients alike.
I manage patients with chronic diseases
I have uploaded my logo and current business card, I would also like the other Certified Clinical Nutritionist logo incorporated into the design

Target Market(s)

Doctors, specialists and patients

Industry/Entity Type

Healthcare

Contact Information for Business Card

www.brightfieldnutrition.com.au
Ph: 0427 561 903
Fax: 6457 2183
email: marcus.k.diet@fernmail.com
Space on the back of the card with: Appointment date, Appointment time and appointment location

Font styles to use
Serif

Colors
fbee3e
876aae
ffc214

Requirements
Must have
• My Logo
• Certified Clinical Nutritionist Logo
• My 4 locations - Pinebrook Medical Centre, North Corrin Health, Hollis Medical, Ashcombe Doctors Surgery
Nice to have
• I like the colours in my current business card

```html
<!DOCTYPE html>
<html lang="en">
<head>
<meta charset="utf-8">
<title>Brightfield Nutrition – Business Card</title>
<link href="https://fonts.googleapis.com/css2?family=Josefin+Slab:wght@400;600&display=swap" rel="stylesheet">
<style>
  :root {
    --backdrop: #e6e7ea;
    --card: #ffffff;
    --navy: #1f2f8f;
    --blue: #2b6cc4;
    --blue-deep: #1d3a9a;
    --green: #7fbf3a;
    --grey-text: #444444;
    --rule: #b9bcc4;
    --wash-a: #e9f0e1;
    --wash-b: #f7f9f4;
    --badge: #dfe3ea;
  }
  * { box-sizing: border-box; margin: 0; padding: 0; }
  html, body { width: 1200px; height: 886px; overflow: hidden; }
  body {
    background: var(--backdrop);
    font-family: "Josefin Slab", serif;
    position: relative;
  }
  .card {
    position: absolute;
    width: 560px;
    height: 320px;
    background: var(--card);
    border-radius: 22px;
    overflow: hidden;
    box-shadow: 0 8px 24px rgba(0,0,0,0.18);
  }

  /* Appointment side */
  .card--appointment { left: 70px; top: 90px; }
  .appointment__wash {
    position: absolute; inset: 0;
    background: linear-gradient(120deg, var(--wash-a) 0%, var(--wash-b) 55%, #ffffff 100%);
  }
  .brand {
    position: absolute; right: 40px; top: 32px;
    display: flex; align-items: center; gap: 10px;
  }
  .brand__dot {
    width: 34px; height: 34px; border-radius: 50%;
    background: var(--blue);
  }
  .brand__name {
    font-size: 28px; font-weight: 600; color: var(--blue);
  }
  .write-line {
    position: absolute; left: 40px; right: 40px;
    border-bottom: 1px solid var(--rule);
  }
  .field {
    position: absolute;
    color: var(--navy); font-size: 19px; font-weight: 600;
    display: flex; align-items: flex-end; gap: 8px;
  }
  .field__line { border-bottom: 1px solid var(--rule); height: 1px; margin-bottom: 5px; }
  .field__suffix { font-size: 14px; font-weight: 600; }
  .locations {
    position: absolute; list-style: none;
    font-size: 17px; color: var(--grey-text);
  }
  .locations li { display: flex; align-items: center; gap: 8px; line-height: 23px; }
  .tickbox { width: 12px; height: 12px; border: 1.5px solid var(--navy); flex: none; }

  /* Contact side */
  .card--contact { left: 570px; top: 476px; }
  .contact__art {
    position: absolute; left: 0; top: 20px;
    width: 290px; height: 280px;
    background: linear-gradient(135deg, var(--blue) 0%, var(--blue-deep) 100%);
    border-radius: 0 0 150px 0;
  }
  .contact__badge {
    position: absolute; right: 40px; top: 34px;
    width: 64px; height: 64px; border-radius: 50%;
    background: var(--badge);
  }
  .contact__details {
    position: absolute; right: 40px; top: 144px;
    text-align: right;
  }
  .person__name { font-size: 30px; color: var(--navy); font-weight: 600; line-height: 1.1; }
  .person__role { font-size: 21px; color: var(--green); font-weight: 600; margin-bottom: 8px; }
  .contact__line { font-size: 19px; color: var(--grey-text); font-weight: 600; line-height: 1.25; }
</style>
</head>
<body>

<section class="card card--appointment">
  <div class="appointment__wash" role="img" aria-label="Soft faded photograph of fresh green vegetables"></div>
  <div class="brand">
    <span class="brand__dot"></span>
    <span class="brand__name">Brightfield Nutrition</span>
  </div>
  <div class="write-line" style="top:112px;"></div>
  <div class="write-line" style="top:146px;"></div>
  <div class="field" style="left:40px; top:196px;">Date :<span class="field__line" style="width:180px;"></span></div>
  <div class="field" style="left:300px; top:170px;">Time :<span class="field__line" style="width:130px;"></span><span class="field__suffix">AM/PM</span></div>
  <ul class="locations" style="left:40px; top:234px;">
    <li><span class="tickbox"></span>Pinebrook Medical Centre</li>
    <li><span class="tickbox"></span>North Corrin Health</li>
  </ul>
  <ul class="locations" style="left:300px; top:208px;">
    <li><span class="tickbox"></span>Ashcombe Doctors Surgery</li>
    <li><span class="tickbox"></span>Hollis Medical</li>
  </ul>
</section>

<section class="card card--contact">
  <div class="contact__art" role="img" aria-label="Large blue illustration of a stomach with a chef's knife"></div>
  <div class="contact__badge" role="img" aria-label="Certified Clinical Nutritionist badge"></div>
  <div class="contact__details">
    <p class="person__name">Marcus Kellaway</p>
    <p class="person__role">Nutritionist &amp; Chef</p>
    <p class="contact__line">0427 561 903</p>
    <p class="contact__line">6457 2183</p>
    <p class="contact__line">marcus.k.diet@fernmail.com</p>
    <p class="contact__line">brightfieldnutrition.com.au</p>
  </div>
</section>

</body>
</html>
```